Real Estate Company Looking for Business Card Designs for 3 Executives

Hello!
Thanks so much for considering our project! We are a real estate investment company located in Edmonton, Alberta called Bellhaven Group of Companies. We invest/develop both commercial and residential real estate and are looking to create 3 DOUBLE-SIDED business cards for 3 top executives in the company! (for some reason it won't let us select the double-sided option, but yes, the cards are double sided and would be happy to tip extra)

We have certain guidelines that we want our business cards to for sure follow - the back of the Business card has to be the Black Background Version of the Logo which has already been designed and linked as a file (first file). We want the entire back of the card to simply just be the black background logo. In terms of the front of the card, would like to see a smaller version of the white background logo (linked as the second file) in the top left hand corner - of course, feel free to get creative and we can make revisions together along the way! and Then after that, just text. We want the card to be sharp, clean, easy on the eyes and highly professional looking. We would like the card to include the Full name of the Company (Bellhaven Group of Companies), Name of the Person, Title, Phone, Email. If possible please provide the front part of the card for 3 people:

1) Bellhaven Group of Companies, Liora Quenby, Chief Financial Officer, 780-555-0142, lioraquenby@bellhavengroup.example

2) Bellhaven Group of Companies, Tobias Quenby, Chief Executive Officer, 780-555-0187, tobiasquenby@bellhavengroup.example

3) Bellhaven Group of Companies, Rui Delcourt, Chief Operations Officer, 587-555-0163, ruidelcourt@bellhavengroup.example

Thank you so much for considering our project & we look forward to seeing your designs!

```html
<!DOCTYPE html>
<html lang="en">
<head>
<meta charset="utf-8">
<title>Bellhaven Business Card – Liora Quenby</title>
<link href="https://fonts.googleapis.com/css2?family=Arimo:wght@400;700&display=swap" rel="stylesheet">
<style>
  :root {
    --backdrop: #2a2a2a;
    --ink: #0d0a0b;
    --paper: #ffffff;
    --muted: #1a1a1a;
    --rule: #333333;
  }
  * { box-sizing: border-box; margin: 0; padding: 0; }
  html, body {
    width: 1200px;
    height: 1015px;
    overflow: hidden;
    background: var(--backdrop);
    font-family: "Arimo", Arial, sans-serif;
  }
  .sheet {
    width: 1200px;
    height: 1015px;
    display: flex;
    flex-direction: column;
    align-items: center;
    justify-content: center;
    gap: 70px;
  }
  .card {
    width: 700px;
    height: 400px;
    position: relative;
    overflow: hidden;
  }

  /* Back of card */
  .card--back {
    background: var(--ink);
    display: flex;
    align-items: center;
    justify-content: center;
  }
  .wordmark {
    display: flex;
    align-items: center;
    gap: 18px;
    font-weight: 400;
    text-transform: uppercase;
    letter-spacing: 0.42em;
  }
  .wordmark__mark {
    width: 14px;
    height: 14px;
  }
  .card--back .wordmark { color: var(--paper); font-size: 30px; }
  .card--back .wordmark__mark { background: var(--paper); }

  /* Front of card */
  .card--front {
    background: var(--paper);
  }
  .front__body {
    position: absolute;
    inset: 0 0 66px 0;
    display: flex;
    align-items: center;
    padding-left: 46px;
  }
  .card--front .wordmark { color: var(--ink); font-size: 19px; gap: 12px; }
  .card--front .wordmark__mark { background: var(--ink); width: 10px; height: 10px; }
  .divider {
    width: 1px;
    height: 110px;
    background: var(--rule);
    margin: 0 28px 0 26px;
  }
  .contact { color: var(--muted); }
  .contact__name {
    font-weight: 700;
    font-size: 19px;
    letter-spacing: 0.02em;
    text-transform: uppercase;
    color: var(--ink);
  }
  .contact__title {
    font-size: 14px;
    margin-top: 2px;
  }
  .contact__list {
    list-style: none;
    margin-top: 22px;
    font-size: 14px;
    line-height: 1.4;
  }
  .contact__list li {
    display: flex;
    align-items: center;
    gap: 6px;
  }
  .contact__icon { width: 12px; height: 12px; flex: none; }
  .front__band {
    position: absolute;
    left: 0; right: 0; bottom: 0;
    height: 66px;
    background: var(--ink);
    color: var(--paper);
    display: flex;
    align-items: center;
    justify-content: center;
    font-size: 15px;
    letter-spacing: 0.01em;
  }
</style>
</head>
<body>
  <main class="sheet">
    <section class="card card--back" aria-label="Card back">
      <div class="wordmark"><span class="wordmark__mark"></span>Bellhaven</div>
    </section>

    <section class="card card--front" aria-label="Card front">
      <div class="front__body">
        <div class="wordmark"><span class="wordmark__mark"></span>Bellhaven</div>
        <div class="divider"></div>
        <div class="contact">
          <p class="contact__name">Liora Quenby</p>
          <p class="contact__title">Chief Financial Officer</p>
          <ul class="contact__list">
            <li>
              <svg class="contact__icon" viewBox="0 0 24 24" aria-hidden="true"><path fill="#0d0a0b" d="M6.6 10.8a15.1 15.1 0 0 0 6.6 6.6l2.2-2.2a1 1 0 0 1 1-.25 11.4 11.4 0 0 0 3.6.57 1 1 0 0 1 1 1V20a1 1 0 0 1-1 1A17 17 0 0 1 3 4a1 1 0 0 1 1-1h3.5a1 1 0 0 1 1 1c0 1.25.2 2.45.57 3.57a1 1 0 0 1-.25 1z"/></svg>
              780-555-0142
            </li>
            <li>
              <svg class="contact__icon" viewBox="0 0 24 24" aria-hidden="true"><path fill="#0d0a0b" d="M2 5h20v14H2zm2 2v.5l8 5 8-5V7l-8 5z"/></svg>
              lioraquenby@bellhavengroup.example
            </li>
          </ul>
        </div>
      </div>
      <div class="front__band">www.bellhavengroup.example</div>
    </section>
  </main>
</body>
</html>
```